MS Word and MS Powerpoint template creation using existing logo as style guide

Create a professional looking MS Word document template and MS powerpoint template for Torvane Advisory Pty Ltd using a logo that's already been created as the style guide. Torvane is a professional services business providing strategy, governance and execution support to small and medium business, Boards and executive teams. refer design brief.

Target Market(s)

Small to medium business, Chairs, Boards, executive teams, general managers

Industry/Entity Type

Professional business services, consultancy, business support outsourcing

Other font styles liked:
• calibri

Requirements
Must have
• leverage the existing logo for colour scheme. Use the TORVANE logo type font. Fully editable templates Word and MS Powerpoint,
Nice to have
• Refer to the design brief
Should not have
• animations, cartoons, stock images of people.

```html
<!DOCTYPE html>
<html lang="en">
<head>
<meta charset="utf-8">
<title>Torvane Presentation Template</title>
<link rel="stylesheet" href="https://fonts.googleapis.com/css2?family=Outfit:wght@300;400;500;600;700&family=Open+Sans:wght@400;600;700&family=Great+Vibes&display=swap">
<style>
:root{
  --page:#94b9ee;
  --navy:#1b2c47;
  --navy-deep:#172842;
  --ink:#243248;
  --muted:#6f7884;
  --blue:#2f7fc4;
  --blue-bright:#3b9ae0;
  --teal:#3fd1cf;
  --sky:#5bb8e8;
  --grey-panel:#f1f2f4;
  --green:#36bd73;
  --red:#ee6a7d;
  --violet:#5b4fa0;
  --line:#c9ced6;
}
*{box-sizing:border-box;margin:0;padding:0}
html,body{width:1056px;height:1200px;overflow:hidden;background:var(--page)}
.board{position:absolute;left:0;top:0;width:1798px;height:2044px;transform:scale(.587319);transform-origin:0 0;font-family:"Open Sans",sans-serif;color:var(--ink)}
.slide{position:absolute;width:541px;height:304px;overflow:hidden;background:#fff}
.abs{position:absolute}
.dark{background:linear-gradient(135deg,#1f3656,#172842)}
.head{font-family:"Outfit",sans-serif}
.kicker{font-family:"Outfit",sans-serif;font-size:15px;letter-spacing:3.2px;color:var(--navy);font-weight:400;text-transform:uppercase}
.title{font-family:"Outfit",sans-serif;font-size:27px;color:var(--navy);font-weight:400;line-height:1.1}
.swoosh{display:block;width:90px;height:6px;margin-top:4px}
.body{font-size:7.6px;line-height:1.45;color:var(--muted)}
.lead{font-size:7.6px;line-height:1.45;color:var(--ink);font-weight:700}
.label{font-family:"Outfit",sans-serif;font-size:9px;line-height:1.2;color:var(--navy);font-weight:500}
.photo{position:absolute}
.card{position:absolute;border:1px solid var(--line);background:#fff;padding:7px 9px;box-shadow:0 2px 4px rgba(0,0,0,.08)}
.navy-box{position:absolute;background:var(--navy);color:#fff;padding:9px 11px}
.navy-box .body{color:#d6dde8}
.pct{font-family:"Outfit",sans-serif;font-size:24px;font-weight:600;color:var(--navy)}
.script{font-family:"Great Vibes",cursive}
.brand-name{font-family:"Outfit",sans-serif;color:#fff;font-size:30px;font-weight:500;display:flex;align-items:center;gap:10px}
.brand-name .dot{width:12px;height:12px;background:var(--blue-bright)}
.agenda-list{position:absolute;font-family:"Outfit",sans-serif;font-size:10.5px;color:var(--ink);line-height:1.2}
.agenda-list li{list-style:none;position:relative;padding-left:17px;height:39px}
.agenda-list li::before{content:"↗";position:absolute;left:0;top:-1px;font-size:10px}
.year-tag{display:inline-block;background:var(--blue);color:#fff;font-size:6px;font-weight:700;padding:2px 7px}
.risk-item{position:absolute;width:135px}
.risk-item .lead{font-size:6.4px;font-weight:600}
.risk-item .body{font-size:6.4px}
.table-wrap{position:absolute;left:22px;top:122px;width:498px;height:170px;background:var(--grey-panel);border-radius:6px;padding:8px 10px}
.grid-table{width:100%;border-collapse:separate;border-spacing:4px 5px;font-size:7px;color:var(--blue)}
.grid-table th{text-align:left;color:var(--navy);font-weight:700;padding:2px 4px}
.grid-table td{background:#fff;padding:5px 4px;border-radius:2px}
</style>
</head>
<body>
<div class="board">

<!-- Cover -->
<section class="slide dark" style="left:628px;top:70px">
  <div class="photo" style="left:0;top:0;width:541px;height:304px;background:radial-gradient(ellipse at 85% 60%,rgba(70,110,150,.35),transparent 60%),radial-gradient(ellipse at 10% 80%,rgba(60,90,130,.3),transparent 55%)" role="img" aria-label="Dark chess pieces background"></div>
  <div class="abs" style="left:0;width:541px;top:68px;display:flex;justify-content:center">
    <div class="brand-name"><span class="dot"></span>Torvane</div>
  </div>
  <div class="abs head" style="left:0;width:541px;top:142px;text-align:center;color:var(--teal);font-size:22px;letter-spacing:5px">CONNECTING</div>
  <div class="abs head" style="left:0;width:541px;top:168px;text-align:center;color:#fff;font-size:28px;font-weight:600">Strategy, Governance</div>
  <div class="abs head" style="left:193px;top:203px;color:#fff;font-size:28px">and</div>
  <div class="abs head" style="left:250px;top:203px;background:var(--blue);color:#fff;font-size:28px;font-weight:600;padding:0 11px;transform:rotate(-2deg)">Execution</div>
</section>

<!-- Agenda -->
<section class="slide" style="left:71px;top:390px">
  <div class="photo" style="left:14px;top:13px;width:172px;height:278px;background:linear-gradient(160deg,#d9d9d9,#5a5a5a 60%,#2b2b2b)" role="img" aria-label="Black and white skyscrapers"></div>
  <div class="abs head" style="left:98px;top:48px;width:132px;height:50px;background:var(--navy);color:#fff;font-size:31px;font-weight:500;text-align:center;line-height:50px">Agenda</div>
  <ul class="agenda-list" style="left:248px;top:42px">
    <li>Executive<br>Summary</li><li>About<br>Torvane Management</li><li>The Problem<br>Opportunity</li><li>Objectives<br>Success Criteria</li><li>Proposed<br>Solution</li><li>Why this<br>Option</li>
  </ul>
  <ul class="agenda-list" style="left:387px;top:42px">
    <li>Risk and<br>Mitigations</li><li>Financial and<br>Resource Impact</li><li>Governance and<br>Accountability</li><li>Implementation Plan<br>&amp; Timeline</li><li>Decision<br>Sought</li><li>Questions and<br>Answers</li>
  </ul>
</section>

<!-- Executive Summary -->
<section class="slide" style="left:628px;top:390px">
  <div class="abs" style="left:30px;top:66px">
    <div class="kicker">Executive ↗</div>
    <div class="title">Summary</div>
    <svg class="swoosh" viewBox="0 0 90 6"><path d="M40 3 H88 M40 3 q6 -3 10 0" stroke="var(--navy)" fill="none" stroke-width="1"/></svg>
  </div>
  <p class="abs lead" style="left:30px;top:137px;width:155px">Lorem ipsum dolor sit amet, consectetur adipiscing elit, sed do eiusmod tempor. Lorem ipsum dolor sit amet, consectetur adipiscing elit,.</p>
  <p class="abs body" style="left:30px;top:188px;width:155px">Lorem ipsum dolor sit amet, consectetur adipiscing elit, sed do eiusmod tempor incididunt ut labore et dolore magna aliqua. Quis ipsum suspendisse ultrices</p>
  <div class="photo" style="left:274px;top:13px;width:253px;height:278px;background:linear-gradient(150deg,#3d4f60,#7c8a92 55%,#2f3b46)" role="img" aria-label="Team collaborating at laptops in an office"></div>
  <div class="navy-box" style="left:207px;top:124px;width:152px;height:133px">
    <div class="script" style="font-size:19px;color:var(--sky);line-height:1">Empowering</div>
    <div class="head" style="font-size:10.5px;line-height:1.2;margin:2px 0 4px">Growth, Innovation<br>and Collaboration</div>
    <p class="body" style="font-size:8.4px">Lorem ipsum dolor sit amet, consectetur adipiscing elit, sed do eiusmod tempor incididunt ut labore et dolore magna aliqua.</p>
  </div>
</section>

<!-- About -->
<section class="slide" style="left:1185px;top:390px">
  <div class="photo" style="left:28px;top:20px;width:200px;height:284px;background:linear-gradient(180deg,#e6e8eb,#3a3f47 55%,#22262c)" role="img" aria-label="Portrait of a consultant in a suit"></div>
  <div class="navy-box" style="left:113px;top:100px;width:120px;height:70px;padding:6px 8px">
    <div class="label" style="color:#fff;font-size:7.4px">Lorem Ipsum<br>Dolor Sit Amet</div>
    <p class="body" style="font-size:7.2px">Lorem ipsum dolor sit amet, consectetur adipiscing elit, sed do eiusmod tempor.</p>
  </div>
  <div class="abs" style="left:252px;top:38px">
    <div class="kicker">About ↗</div>
    <div class="title">Torvane Management</div>
  </div>
  <p class="abs body" style="left:252px;top:97px;width:215px;color:var(--ink);font-size:8.4px">Lorem ipsum dolor sit amet, consectetur adipiscing elit, sed do eiusmod tempor. Lorem ipsum dolor sit</p>
  <p class="abs body" style="left:252px;top:126px;width:240px">Lorem ipsum dolor sit amet, consectetur adipiscing elit, sed do eiusmod tempor incididunt ut labore et dolore magna aliqua. Quis ipsum suspendisse ultrices gravida. Risus commodo viverra maecenas accumsan lacus vel facilisis.</p>
  <div class="card" style="left:252px;top:205px;width:118px;height:70px">
    <svg class="abs" style="right:8px;top:6px" width="20" height="16" viewBox="0 0 20 16"><circle cx="10" cy="4" r="3.5" fill="var(--navy)"/><circle cx="3.5" cy="6" r="2.5" fill="var(--navy)"/><circle cx="16.5" cy="6" r="2.5" fill="var(--navy)"/><path d="M4 16 q6-10 12 0z M0 15 q3.5-7 6-3 M20 15 q-3.5-7-6-3" fill="var(--navy)"/></svg>
    <div class="label" style="font-size:7.4px">Lorem Ipsum<br>Dolor Sit Amet</div>
    <p class="body" style="font-size:7.2px">Lorem ipsum dolor sit amet, consectetur adipiscing elit, sed do eiusmod tempor.</p>
  </div>
  <div class="card" style="left:377px;top:205px;width:118px;height:70px">
    <svg class="abs" style="right:8px;top:6px" width="18" height="16" viewBox="0 0 18 16"><circle cx="9" cy="4" r="3.5" fill="var(--navy)"/><path d="M2 16 q7-12 14 0z" fill="var(--navy)"/></svg>
    <div class="label" style="font-size:7.4px">Lorem Ipsum<br>Dolor Sit Amet</div>
    <p class="body" style="font-size:7.2px">Lorem ipsum dolor sit amet, consectetur adipiscing elit, sed do eiusmod tempor.</p>
  </div>
</section>

<!-- Problem / Opportunity -->
<section class="slide" style="left:71px;top:710px">
  <div class="abs" style="left:0;top:0;width:210px;height:304px;background:var(--grey-panel)"></div>
  <div class="abs" style="left:30px;top:66px">
    <div class="kicker">The Problem ↗</div>
    <div class="title">Opportunity</div>
    <svg class="swoosh" viewBox="0 0 90 6"><path d="M55 3 H145 M55 3 q6 -3 10 0" stroke="var(--navy)" fill="none" stroke-width="1"/></svg>
  </div>
  <p class="abs lead" style="left:30px;top:137px;width:155px">Lorem ipsum dolor sit amet, consectetur adipiscing elit, sed do eiusmod tempor. Lorem ipsum dolor sit amet, consectetur adipiscing elit,.</p>
  <p class="abs body" style="left:30px;top:188px;width:155px">Lorem ipsum dolor sit amet, consectetur adipiscing elit, sed do eiusmod tempor incididunt ut labore et dolore magna aliqua. Quis ipsum suspendisse ultrices</p>
  <p class="abs body" style="left:229px;top:37px;width:215px;color:var(--ink)">Lorem ipsum dolor sit amet, consectetur adipiscing elit, sed do eiusmod tempor incididunt ut labore et dolore magna aliqua, incididunt ut labore et dolore magna aliqua.</p>
  <div class="abs" style="left:230px;top:86px;width:118px">
    <svg width="24" height="24" viewBox="0 0 24 24"><circle cx="12" cy="12" r="8" fill="none" stroke="var(--navy)" stroke-width="1.6"/><path d="M12 4 V1 M12 23 V20 M4 12 H1 M23 12 H20" stroke="var(--navy)" stroke-width="1.6"/><circle cx="12" cy="12" r="3" fill="var(--navy)"/></svg>
    <div class="label" style="margin-top:6px">Lorem ipsum<br>dolor sit</div>
    <p class="body">Lorem ipsum dolor sit amet, consectetur adipiscing elit, sed do eiusmod tempor incididunt</p>
  </div>
  <div class="abs" style="left:357px;top:86px;width:118px">
    <svg width="24" height="24" viewBox="0 0 24 24"><circle cx="12" cy="12" r="8" fill="none" stroke="var(--navy)" stroke-width="1.6"/><path d="M12 7 v10 M9.5 9.5 h4 a1.5 1.5 0 0 1 0 3 h-3 a1.5 1.5 0 0 0 0 3 h4" stroke="var(--navy)" fill="none" stroke-width="1.3"/></svg>
    <div class="label" style="margin-top:6px">Lorem ipsum<br>dolor sit</div>
    <p class="body">Lorem ipsum dolor sit amet, consectetur adipiscing elit, sed do eiusmod tempor incididunt</p>
  </div>
  <div class="card" style="left:357px;top:210px;width:160px;height:50px;box-shadow:none">
    <p class="body">Lorem ipsum dolor sit amet, consectetur adipiscing elit, sed do eiusmod tempor incididunt ut labore et dolore magna</p>
  </div>
  <div class="navy-box" style="left:230px;top:200px;width:127px;height:70px">
    <p class="body" style="color:#fff">Lorem ipsum dolor sit amet, consectetur adipiscing elit, sed do eiusmod tempor, incididunt ut labore et dolore</p>
  </div>
</section>

<!-- Objectives -->
<section class="slide" style="left:628px;top:710px">
  <div class="abs" style="left:30px;top:40px">
    <div class="kicker">Objeectives ↗</div>
    <div class="title">Success Criteria</div>
    <svg class="swoosh" viewBox="0 0 90 6"><path d="M0 3 H90 M40 3 q6 -3 10 0" stroke="var(--navy)" fill="none" stroke-width="1"/></svg>
  </div>
  <p class="abs lead" style="left:30px;top:103px;width:175px">Lorem ipsum dolor sit amet, consectetur adipiscing elit, sed do eiusmod tempor. Lorem ipsum dolor sit amet, consectetur adipiscing</p>
  <div class="abs pct" style="left:28px;top:148px">52%</div>
  <p class="abs body" style="left:86px;top:152px;width:80px">Lorem ipsum dolor sit amet, consectetur adipiscing elit, sed do</p>
  <div class="card" style="left:29px;top:200px;width:118px;height:71px">
    <div class="label" style="font-size:7.4px">Lorem Ipsum<br>Dolor Sit Amet</div>
    <p class="body" style="font-size:7.2px">Lorem ipsum dolor sit amet, consectetur adipiscing elit, sed do eiusmod tempor.</p>
  </div>
  <svg class="abs" style="left:238px;top:55px" width="200" height="160" viewBox="0 0 200 160">
    <rect x="14" y="62" width="50" height="50" transform="rotate(45 39 87)" fill="var(--navy)"/>
    <rect x="50" y="98" width="50" height="50" transform="rotate(45 75 123)" fill="#1f66a5"/>
    <rect x="86" y="62" width="50" height="50" transform="rotate(45 111 87)" fill="#2e9bd6"/>
    <rect x="122" y="26" width="50" height="50" transform="rotate(45 147 51)" fill="var(--teal)"/>
    <circle cx="39" cy="84" r="5" fill="#fff"/><path d="M75 115 l4 10 h-8z" fill="#fff"/>
    <path d="M103 87 l8 -5 l8 5 l-8 5z" fill="#fff"/><rect x="141" y="46" width="3" height="8" fill="#fff"/><rect x="146" y="43" width="3" height="11" fill="#fff"/><rect x="151" y="48" width="3" height="6" fill="#fff"/>
  </svg>
  <div class="abs pct" style="left:232px;top:155px;font-size:22px">01</div>
  <div class="abs pct" style="left:302px;top:214px;font-size:22px;color:#1f66a5">02</div>
  <div class="abs pct" style="left:370px;top:160px;font-size:22px;color:#2e9bd6">03</div>
  <div class="abs pct" style="left:412px;top:56px;font-size:22px;color:var(--teal)">04</div>
  <p class="abs body" style="left:413px;top:22px;width:80px">Lorem ipsum dolor sit amet, consectetur adipiscing elit, sed do</p>
  <p class="abs body" style="left:180px;top:186px;width:80px;text-align:right">Lorem ipsum dolor sit amet, consectetur adipiscing elit, sed do</p>
  <p class="abs body" style="left:372px;top:190px;width:108px">Lorem ipsum dolor sit amet, consectetur adipiscing elit, sed do eiusmod tempor incididunt</p>
  <p class="abs body" style="left:262px;top:246px;width:108px;text-align:center">Lorem ipsum dolor sit amet, consectetur adipiscing elit, sed do eiusmod tempor incididunt</p>
</section>

<!-- Proposed Solution -->
<section class="slide" style="left:1185px;top:710px;background:var(--grey-panel)">
  <div class="abs" style="left:30px;top:32px">
    <div class="kicker">Purposed ↗</div>
    <div class="title">Solutuion</div>
    <svg class="swoosh" viewBox="0 0 90 6"><path d="M0 3 H90 M40 3 q6 -3 10 0" stroke="var(--navy)" fill="none" stroke-width="1"/></svg>
  </div>
  <p class="abs body" style="left:177px;top:33px;width:290px">Lorem ipsum dolor sit amet, consectetur adipiscing elit, sed do eiusmod tempor incididunt ut labore et dolore magna aliqua. Quis ipsum suspendisse ultrices gravida. Risus commodo viverra maecenas accumsan lacus vel facilisis.</p>
  <svg class="abs" style="left:180px;top:80px" width="180" height="130" viewBox="0 0 180 130">
    <path d="M60 40 A35 35 0 0 0 125 40" stroke="url(#arc)" stroke-width="2" fill="none"/>
    <defs><linearGradient id="arc"><stop offset="0" stop-color="#f0a030"/><stop offset=".5" stop-color="#3b9ae0"/><stop offset="1" stop-color="#b04fc0"/></linearGradient></defs>
    <circle cx="91" cy="28" r="24" fill="#fff" stroke="#e2e4e8"/>
    <g fill="#fff" stroke="#e2e4e8">
      <circle cx="22" cy="46" r="17"/><circle cx="46" cy="92" r="17"/><circle cx="90" cy="112" r="17"/><circle cx="135" cy="92" r="17"/><circle cx="159" cy="46" r="17"/>
    </g>
    <path d="M17 51 l8 -8 l2 2 l-8 8z" fill="var(--navy)"/>
    <circle cx="45" cy="90" r="4" fill="none" stroke="var(--navy)" stroke-width="1.4"/><path d="M42 93 l-3 3" stroke="var(--navy)" stroke-width="1.4"/>
    <circle cx="90" cy="108" r="3" fill="var(--navy)"/><path d="M84 118 q6-8 12 0z" fill="var(--navy)"/>
    <rect x="129" y="87" width="12" height="8" fill="none" stroke="var(--navy)" stroke-width="1.3"/>
    <path d="M153 41 h2 M153 46 h2 M153 51 h2 M157 41 h9 M157 46 h9 M157 51 h9" stroke="var(--navy)" stroke-width="1.6"/>
  </svg>
  <div class="abs label" style="left:247px;top:96px;width:48px;text-align:center;font-size:8.5px">Lorem<br>Ipsum</div>
  <div class="abs" style="left:85px;top:134px;width:85px;text-align:right"><div class="label" style="font-size:7.4px">Lorem Ipsum<br>Dolor Sit Amet</div><p class="body">Lorem ipsum dolor sit amet, consectetur adipiscing elit, sed do</p></div>
  <div class="abs" style="left:371px;top:134px;width:85px"><div class="label" style="font-size:7.4px">Lorem Ipsum<br>Dolor Sit Amet</div><p class="body">Lorem ipsum dolor sit amet, consectetur adipiscing elit, sed do</p></div>
  <div class="abs" style="left:125px;top:204px;width:85px;text-align:right"><div class="label" style="font-size:7.4px">Lorem Ipsum<br>Dolor Sit Amet</div><p class="body">Lorem ipsum dolor sit amet, consectetur adipiscing elit, sed do</p></div>
  <div class="abs" style="left:338px;top:204px;width:85px"><div class="label" style="font-size:7.4px">Lorem Ipsum<br>Dolor Sit Amet</div><p class="body">Lorem ipsum dolor sit amet, consectetur adipiscing elit, sed do</p></div>
  <div class="abs" style="left:228px;top:217px;width:85px;text-align:center"><div class="label" style="font-size:7.4px">Lorem Ipsum<br>Dolor Sit Amet</div><p class="body">Lorem ipsum dolor sit amet, consectetur adipiscing elit, sed do</p></div>
</section>

<!-- Why this option -->
<section class="slide" style="left:71px;top:1030px">
  <div class="abs" style="left:30px;top:38px">
    <div class="kicker">Why this ↗</div>
    <div class="title">Option</div>
    <svg class="swoosh" viewBox="0 0 90 6"><path d="M40 3 H112 M40 3 q6 -3 10 0" stroke="var(--navy)" fill="none" stroke-width="1"/></svg>
  </div>
  <p class="abs body" style="left:30px;top:105px;width:215px">Lorem ipsum dolor sit amet, consectetur adipiscing elit, sed do eiusmod tempor incididunt ut labore et dolore magna aliqua. Quis ipsum suspendisse ultrices gravida. Risus commodo viverra maecenas accumsan lacus vel facilisis.</p>
  <div class="abs" style="left:30px;top:164px;width:165px">
    <p class="body" style="padding-left:12px;position:relative;margin-bottom:6px"><span style="position:absolute;left:0;color:var(--blue)">↗</span>Lorem ipsum dolor sit amet, consectetur adipiscing elit, sed do eiusmod tempor</p>
    <p class="body" style="padding-left:12px;position:relative;margin-bottom:6px"><span style="position:absolute;left:0;color:var(--blue)">↗</span>Lorem ipsum dolor sit amet, consectetur adipiscing elit, sed do eiusmod tempor incididunt ut labore</p>
    <p class="body" style="padding-left:12px;position:relative"><span style="position:absolute;left:0;color:var(--blue)">↗</span>Lorem ipsum dolor sit amet, consectetur adipiscing elit, sed do eiusmod tempor</p>
  </div>
  <div class="photo" style="left:274px;top:17px;width:113px;height:88px;background:linear-gradient(150deg,#5b8fc4,#2e5a86)" role="img" aria-label="Team meeting with charts on screen"></div>
  <div class="photo" style="left:389px;top:108px;width:113px;height:88px;background:linear-gradient(150deg,#6e7b84,#2a343c)" role="img" aria-label="Colleagues discussing in a glass office"></div>
  <div class="photo" style="left:274px;top:198px;width:113px;height:88px;background:linear-gradient(150deg,#e4e6ea,#8b8f96)" role="img" aria-label="Professional working on a laptop"></div>
  <div class="abs" style="left:398px;top:22px;width:112px"><div class="label" style="font-size:9px;font-family:'Open Sans',sans-serif;font-weight:400">Lorem Ipsum<br>Dolor Sit Amet</div><p class="body">Lorem ipsum dolor sit amet, consectetur adipiscing elit, sed do eiusmod tempor. incididunt ut labore et dolore</p></div>
  <div class="abs" style="left:274px;top:113px;width:112px"><div class="label" style="font-size:9px;font-family:'Open Sans',sans-serif;font-weight:400">Lorem Ipsum<br>Dolor Sit Amet</div><p class="body">Lorem ipsum dolor sit amet, consectetur adipiscing elit, sed do eiusmod tempor. incididunt ut labore et dolore</p></div>
  <div class="abs" style="left:398px;top:207px;width:112px"><div class="label" style="font-size:9px;font-family:'Open Sans',sans-serif;font-weight:400">Lorem Ipsum<br>Dolor Sit Amet</div><p class="body">Lorem ipsum dolor sit amet, consectetur adipiscing elit, sed do eiusmod tempor. incididunt ut labore et dolore</p></div>
</section>

<!-- Risk & Mitigations -->
<section class="slide" style="left:628px;top:1030px">
  <div class="abs" style="left:0;width:541px;top:24px;text-align:center">
    <div class="title" style="display:inline-block">Risk &amp; Mitigations <span style="font-size:16px;vertical-align:top">↗</span></div>
    <svg class="swoosh" style="margin:0 auto" viewBox="0 0 90 6"><path d="M20 3 H90 M40 3 q6 -3 10 0" stroke="var(--navy)" fill="none" stroke-width="1"/></svg>
  </div>
  <p class="abs body" style="left:108px;top:70px;width:325px;text-align:center">Lorem ipsum dolor sit amet, consectetur adipiscing elit, sed do eiusmod tempor incididunt ut labore et dolore magna aliqua. Quis ipsum suspendisse ultrices gravida. Risus commodo</p>
  <svg class="abs" style="left:260px;top:108px" width="22" height="166" viewBox="0 0 22 166"><path d="M0 6 L11 0 L22 6 V160 L11 166 L0 160z" fill="var(--navy)"/></svg>
  <div class="abs head" style="left:258px;top:190px;width:26px;transform:rotate(-90deg);transform-origin:center;color:#fff;font-size:8px;white-space:nowrap;text-align:center;line-height:26px">Risk Management</div>
  <div class="risk-item" style="left:112px;top:112px;text-align:right"><span class="year-tag">2014</span><p class="lead" style="color:var(--navy)">Lorem Ipsum Dolor Sit Amet</p><p class="body">Lorem ipsum dolor sit amet, consectetur adipiscing elit, sed do eiusmod tempor.</p></div>
  <div class="risk-item" style="left:112px;top:170px;text-align:right"><span class="year-tag">2015</span><p class="lead" style="color:var(--navy)">Lorem Ipsum Dolor Sit Amet</p><p class="body">Lorem ipsum dolor sit amet, consectetur adipiscing elit, sed do eiusmod tempor.</p></div>
  <div class="risk-item" style="left:112px;top:227px;text-align:right"><span class="year-tag">2016</span><p class="lead" style="color:var(--navy)">Lorem Ipsum Dolor Sit Amet</p><p class="body">Lorem ipsum dolor sit amet, consectetur adipiscing elit, sed do eiusmod tempor.</p></div>
  <div class="risk-item" style="left:297px;top:112px"><span class="year-tag">2017</span><p class="lead" style="color:var(--navy)">Lorem Ipsum Dolor Sit Amet</p><p class="body">Lorem ipsum dolor sit amet, consectetur adipiscing elit, sed do eiusmod tempor.</p></div>
  <div class="risk-item" style="left:297px;top:170px"><span class="year-tag">2018</span><p class="lead" style="color:var(--navy)">Lorem Ipsum Dolor Sit Amet</p><p class="body">Lorem ipsum dolor sit amet, consectetur adipiscing elit, sed do eiusmod tempor.</p></div>
  <div class="risk-item" style="left:297px;top:227px"><span class="year-tag">2019</span><p class="lead" style="color:var(--navy)">Lorem Ipsum Dolor Sit Amet</p><p class="body">Lorem ipsum dolor sit amet, consectetur adipiscing elit, sed do eiusmod tempor.</p></div>
</section>

<!-- Financial -->
<section class="slide" style="left:1185px;top:1030px">
  <div class="abs" style="left:28px;top:58px">
    <div class="kicker">Financial and ↗</div>
    <div class="title">Resources Impact</div>
    <svg class="swoosh" viewBox="0 0 90 6"><path d="M55 3 H145 M55 3 q6 -3 10 0" stroke="var(--navy)" fill="none" stroke-width="1"/></svg>
  </div>
  <p class="abs lead" style="left:30px;top:130px;width:175px">Lorem ipsum dolor sit amet, consectetur adipiscing elit, sed do eiusmod tempor. Lorem ipsum dolor sit amet, consectetur adipiscing</p>
  <div class="abs pct" style="left:28px;top:178px">52%</div>
  <div class="abs" style="left:82px;top:190px;width:4px;height:12px;background:var(--green);border-radius:2px"></div>
  <div class="abs" style="left:115px;top:180px;width:1px;height:55px;background:var(--line)"></div>
  <div class="abs pct" style="left:127px;top:178px">48%</div>
  <div class="abs" style="left:178px;top:190px;width:4px;height:12px;background:#e23b4e;border-radius:2px"></div>
  <p class="abs body" style="left:30px;top:215px;width:78px">Lorem ipsum dolor sit amet, consectetur adipiscing elit, sed do</p>
  <p class="abs body" style="left:127px;top:215px;width:78px">Lorem ipsum dolor sit amet, consectetur adipiscing elit, sed do</p>
  <svg class="abs" style="left:250px;top:90px" width="260" height="140" viewBox="0 0 260 140">
    <line x1="6" y1="76" x2="252" y2="76" stroke="#9aa1aa" stroke-width="1"/>
    <circle cx="6" cy="76" r="4" fill="var(--green)"/><circle cx="252" cy="76" r="4" fill="var(--red)"/>
    <g fill="var(--green)">
      <rect x="16" y="56" width="11" height="18" rx="2"/><rect x="39" y="36" width="11" height="38" rx="2"/><rect x="62" y="40" width="11" height="34" rx="2"/><rect x="85" y="15" width="11" height="59" rx="2"/><rect x="108" y="23" width="11" height="51" rx="2"/>
    </g>
    <g fill="var(--red)">
      <rect x="136" y="78" width="11" height="18" rx="2"/><rect x="159" y="78" width="11" height="38" rx="2"/><rect x="182" y="78" width="11" height="33" rx="2"/><rect x="205" y="78" width="11" height="44" rx="2"/><rect x="228" y="78" width="11" height="38" rx="2"/>
    </g>
    <g font-family="Open Sans,sans-serif" font-size="6.5" font-weight="700" fill="var(--ink)" text-anchor="middle">
      <text x="21" y="52">15%</text><text x="44" y="32">38%</text><text x="67" y="36">27%</text><text x="90" y="11">62%</text><text x="113" y="19">54%</text>
      <text x="141" y="105">13%</text><text x="164" y="125">39%</text><text x="187" y="120">31%</text><text x="210" y="132">47%</text><text x="233" y="125">40%</text>
    </g>
    <rect x="44" y="84" width="48" height="7" rx="3.5" fill="var(--green)"/><text x="68" y="89.5" font-size="4.5" fill="#fff" text-anchor="middle" font-family="Open Sans,sans-serif">JANUARY - JUNE</text>
    <rect x="162" y="63" width="48" height="7" rx="3.5" fill="var(--red)"/><text x="186" y="68.5" font-size="4.5" fill="#fff" text-anchor="middle" font-family="Open Sans,sans-serif">JANUARY - JUNE</text>
  </svg>
  <div class="card" style="left:393px;top:64px;width:119px;height:71px;border-color:var(--green);box-shadow:none">
    <div class="label" style="font-size:7.4px">Lorem Ipsum<br>Dolor Sit Amet</div>
    <p class="body" style="font-size:7.2px">Lorem ipsum dolor sit amet, consectetur adipiscing elit, sed do eiusmod tempor.</p>
  </div>
  <div class="card" style="left:251px;top:200px;width:118px;height:71px;border-color:var(--red);box-shadow:none">
    <div class="label" style="font-size:7.4px">Lorem Ipsum<br>Dolor Sit Amet</div>
    <p class="body" style="font-size:7.2px">Lorem ipsum dolor sit amet, consectetur adipiscing elit, sed do eiusmod tempor.</p>
  </div>
</section>

<!-- Governance -->
<section class="slide" style="left:71px;top:1350px">
  <div class="photo" style="left:0;top:0;width:541px;height:145px;background:linear-gradient(100deg,#3a78b8,#2a64a4 50%,#4d8ccc)" role="img" aria-label="Chess pieces in blue tones with a financial chart overlay"></div>
  <div class="abs" style="left:27px;top:163px">
    <div class="kicker">Governance and ↗</div>
    <div class="title">Accountability</div>
    <svg class="swoosh" viewBox="0 0 90 6"><path d="M55 3 H145 M55 3 q6 -3 10 0" stroke="var(--navy)" fill="none" stroke-width="1"/></svg>
  </div>
  <p class="abs lead" style="left:27px;top:234px;width:175px">Lorem ipsum dolor sit amet, consectetur adipiscing elit, sed do eiusmod tempor. Lorem ipsum dolor sit amet, consectetur adipiscing</p>
  <div class="card" style="left:264px;top:113px;width:116px;height:70px"><div class="label" style="font-size:7.4px">Lorem Ipsum<br>Dolor Sit Amet</div><p class="body" style="font-size:7.2px">Lorem ipsum dolor sit amet, consectetur adipiscing elit, sed do eiusmod tempor.</p></div>
  <div class="card" style="left:395px;top:113px;width:116px;height:70px"><div class="label" style="font-size:7.4px">Lorem Ipsum<br>Dolor Sit Amet</div><p class="body" style="font-size:7.2px">Lorem ipsum dolor sit amet, consectetur adipiscing elit, sed do eiusmod tempor.</p></div>
  <div class="card" style="left:264px;top:197px;width:116px;height:70px"><div class="label" style="font-size:7.4px">Lorem Ipsum<br>Dolor Sit Amet</div><p class="body" style="font-size:7.2px">Lorem ipsum dolor sit amet, consectetur adipiscing elit, sed do eiusmod tempor.</p></div>
  <div class="card" style="left:395px;top:197px;width:116px;height:70px"><div class="label" style="font-size:7.4px">Lorem Ipsum<br>Dolor Sit Amet</div><p class="body" style="font-size:7.2px">Lorem ipsum dolor sit amet, consectetur adipiscing elit, sed do eiusmod tempor.</p></div>
</section>

<!-- Implementation -->
<section class="slide" style="left:628px;top:1350px">
  <div class="abs" style="left:28px;top:33px">
    <div class="kicker">Implementation Plan ↗</div>
    <div class="title">And Timeline</div>
    <svg class="swoosh" viewBox="0 0 90 6"><path d="M55 3 H145 M55 3 q6 -3 10 0" stroke="var(--navy)" fill="none" stroke-width="1"/></svg>
  </div>
  <svg class="abs" style="left:120px;top:40px" width="360" height="230" viewBox="0 0 360 230">
    <defs><linearGradient id="tl" x1="0" x2="1"><stop offset="0" stop-color="var(--violet)"/><stop offset="1" stop-color="#1a8fa0"/></linearGradient></defs>
    <path d="M50 195 L10 175 V150 L80 115 L180 160 L140 140 V105 L210 65 L300 112 L270 95 V70 L340 23" stroke="url(#tl)" stroke-width="1.4" fill="none"/>
    <g>
      <polygon points="50,188 64,195 50,202 36,195" fill="var(--violet)"/>
      <polygon points="80,108 94,115 80,122 66,115" fill="#4a5fa8"/>
      <polygon points="180,153 194,160 180,167 166,160" fill="#3e6aa8"/>
      <polygon points="210,58 224,65 210,72 196,65" fill="#3a72a8"/>
      <polygon points="300,105 314,112 300,119 286,112" fill="#2a80a4"/>
      <polygon points="340,16 354,23 340,30 326,23" fill="var(--violet)"/>
    </g>
    <g font-family="Outfit,sans-serif" font-size="9.5" font-weight="600" fill="var(--navy)">
      <text x="72" y="202">1997</text><text x="70" y="141">2005</text><text x="172" y="140">2014</text><text x="170" y="57">2018</text><text x="320" y="130">2020</text><text x="330" y="44">2024</text>
    </g>
  </svg>
  <p class="abs body" style="left:68px;top:110px;width:110px">Lorem ipsum dolor sit amet, consectetur adipiscing elit, sed do eiusmod tempor. incididunt ut labore et dolore magna aliqua.</p>
  <p class="abs body" style="left:48px;top:244px;width:110px">Lorem ipsum dolor sit amet, consectetur adipiscing elit, sed do eiusmod tempor.</p>
  <p class="abs body" style="left:290px;top:52px;width:110px">Lorem ipsum dolor sit amet, consectetur adipiscing elit, sed do eiusmod tempor.</p>
  <p class="abs body" style="left:301px;top:218px;width:110px">Lorem ipsum dolor sit amet, consectetur adipiscing elit, sed do eiusmod tempor.</p>
  <p class="abs body" style="left:449px;top:92px;width:80px">Lorem ipsum dolor sit amet, consectetur adipiscing elit, sed do</p>
  <p class="abs body" style="left:439px;top:178px;width:82px">Lorem ipsum dolor sit amet, consectetur adipiscing elit, sed do</p>
</section>

<!-- Decision Sought -->
<section class="slide" style="left:1185px;top:1350px">
  <div class="abs" style="left:28px;top:75px">
    <div class="kicker">Decision ↗</div>
    <div class="title">Sought</div>
    <svg class="swoosh" viewBox="0 0 90 6"><path d="M40 3 H112 M40 3 q6 -3 10 0" stroke="var(--navy)" fill="none" stroke-width="1"/></svg>
  </div>
  <p class="abs lead" style="left:28px;top:144px;width:185px">Lorem ipsum dolor sit amet, consectetur adipiscing elit, sed do eiusmod tempor. Lorem ipsum dolor sit amet, consectetur adipiscing</p>
  <p class="abs body" style="left:28px;top:184px;width:185px">Lorem ipsum dolor sit amet, consectetur adipiscing elit, sed do eiusmod tempor incididunt ut labore et dolore magna aliqua. Quis ipsum suspendisse ultrices gravida. Risus commodo viverra maecenas accumsan lacus vel facilisis.</p>
  <div class="photo" style="left:231px;top:13px;width:134px;height:150px;background:linear-gradient(160deg,#4a4e56,#23262c 60%,#6a5a44)" role="img" aria-label="Team presentation in a dim meeting room"></div>
  <div class="photo" style="left:391px;top:171px;width:136px;height:118px;background:linear-gradient(150deg,#0f2a5a,#2566b0 55%,#f0a040)" role="img" aria-label="Glowing financial growth chart"></div>
  <div class="abs" style="left:405px;top:34px;width:115px"><div class="label" style="font-size:9px;font-family:'Open Sans',sans-serif;font-weight:400">Lorem Ipsum<br>Dolor Sit Amet</div><p class="body">Lorem ipsum dolor sit amet, consectetur adipiscing elit, sed do eiusmod tempor. incididunt ut labore et dolore</p><p class="body" style="margin-top:6px">Lorem ipsum dolor sit amet, consectetur adipiscing elit, sed do eiusmod tempor.</p></div>
  <div class="abs" style="left:239px;top:176px;width:148px"><div class="label" style="font-size:9px;font-family:'Open Sans',sans-serif;font-weight:400">Lorem Ipsum Dolor Sit Amet</div><p class="body" style="margin-top:4px">Lorem ipsum dolor sit amet, consectetur adipiscing elit, sed do eiusmod tempor. incididunt ut labore et dolore magna</p><p class="lead" style="margin-top:4px;font-weight:600">Lorem ipsum dolor sit amet, consectetur adipiscing elit, sed do</p></div>
</section>

<!-- Questions and Answers -->
<section class="slide dark" style="left:71px;top:1670px">
  <div class="photo" style="left:240px;top:0;width:301px;height:304px;background:radial-gradient(ellipse at 45% 40%,rgba(120,190,240,.55),transparent 45%),radial-gradient(ellipse at 60% 80%,rgba(80,140,200,.35),transparent 55%)" role="img" aria-label="Hand holding a glowing question mark"></div>
  <div class="abs head" style="left:50px;top:92px;color:#fff;font-size:32px;font-weight:600;line-height:1.1">Questions</div>
  <div class="abs head" style="left:50px;top:130px;color:#fff;font-size:32px;line-height:1.1">and</div>
  <div class="abs head" style="left:112px;top:124px;background:var(--blue);color:#fff;font-size:32px;font-weight:600;padding:0 10px;transform:rotate(-3deg)">Answers</div>
</section>

<!-- Table -->
<section class="slide" style="left:628px;top:1670px">
  <div class="abs" style="left:28px;top:36px">
    <div class="kicker">Lorem Ipsum ↗</div>
    <div class="title">Lorem Ipsum</div>
    <svg class="swoosh" viewBox="0 0 90 6"><path d="M55 3 H145 M55 3 q6 -3 10 0" stroke="var(--navy)" fill="none" stroke-width="1"/></svg>
  </div>
  <p class="abs body" style="left:193px;top:38px;width:300px;color:var(--ink)">Lorem ipsum dolor sit amet, consectetur adipiscing elit, sed do eiusmod tempor.<br>Lorem ipsum dolor sit amet, consectetur adipiscing elit.</p>
  <p class="abs body" style="left:193px;top:64px;width:230px">Lorem ipsum dolor sit amet, consectetur adipiscing elit, sed do eiusmod tempor. incididunt ut labore et dolore magna aliqua. Quis ipsum suspendisse ultrices gravida. Risus commodo viverra</p>
  <div class="table-wrap">
    <table class="grid-table">
      <tr><th>Lorem Ipsum</th><th>Lorem Ipsum</th><th>Lorem Ipsum</th><th>Lorem Ipsum</th><th>Lorem Ipsum</th><th>Lorem Ipsum</th></tr>
      <tr><td>Lorem Ipsum</td><td>Lorem Ipsum</td><td>Lorem Ipsum</td><td>Lorem Ipsum</td><td>Lorem Ipsum</td><td>Lorem Ipsum</td></tr>
      <tr><td>Lorem Ipsum</td><td>Lorem Ipsum</td><td>Lorem Ipsum</td><td>Lorem Ipsum</td><td>Lorem Ipsum</td><td>Lorem Ipsum</td></tr>
      <tr><td>Lorem Ipsum</td><td>Lorem Ipsum</td><td>Lorem Ipsum</td><td>Lorem Ipsum</td><td>Lorem Ipsum</td><td>Lorem Ipsum</td></tr>
      <tr><td>Lorem Ipsum</td><td>Lorem Ipsum</td><td>Lorem Ipsum</td><td>Lorem Ipsum</td><td>Lorem Ipsum</td><td>Lorem Ipsum</td></tr>
      <tr><td>Lorem Ipsum</td><td>Lorem Ipsum</td><td>Lorem Ipsum</td><td>Lorem Ipsum</td><td>Lorem Ipsum</td><td>Lorem Ipsum</td></tr>
    </table>
  </div>
</section>

<!-- Thank you -->
<section class="slide dark" style="left:1185px;top:1670px">
  <div class="abs script" style="left:38px;top:72px;color:var(--blue-bright);font-size:46px;transform:rotate(-4deg)">Thank you!</div>
  <div class="abs" style="left:44px;top:168px;font-size:9px;color:#fff;line-height:1.3">
    <div style="position:relative;padding-left:16px;margin-bottom:6px"><svg class="abs" style="left:0;top:1px" width="9" height="9" viewBox="0 0 10 10"><path d="M2 0 l2 2.5 -1.2 1.4 q1.2 2.3 3.3 3.3 l1.4-1.2 2.5 2 -1.5 2 q-6-1-8.5-8.5z" fill="#fff"/></svg>(+1) 555 010 2840</div>
    <div style="position:relative;padding-left:16px"><svg class="abs" style="left:1px;top:1px" width="8" height="10" viewBox="0 0 8 10"><path d="M4 0 a4 4 0 0 1 4 4 q0 2.5-4 6 q-4-3.5-4-6 a4 4 0 0 1 4-4z" fill="#fff"/><circle cx="4" cy="4" r="1.4" fill="var(--navy)"/></svg>Lorem ipsum dolor<br>sit amet, City, USA.</div>
  </div>
  <div class="abs" style="left:168px;top:168px;font-size:9px;color:#fff;line-height:1.3">
    <div style="position:relative;padding-left:15px;margin-bottom:9px"><svg class="abs" style="left:0;top:2px" width="10" height="7" viewBox="0 0 10 7"><rect width="10" height="7" fill="#fff"/><path d="M0 0 l5 4 5-4" stroke="var(--navy)" fill="none" stroke-width=".8"/></svg>info@torvane.com</div>
    <div style="position:relative;padding-left:15px"><svg class="abs" style="left:1px;top:1px" width="8" height="10" viewBox="0 0 8 10"><path d="M0 0 L7 6 H4 L5.5 9.5 4.3 10 2.8 6.5 0 9z" fill="#fff"/></svg>www.torvane.com</div>
  </div>
  <div class="abs" style="left:350px;top:132px">
    <div class="brand-name"><span class="dot"></span>Torvane</div>
  </div>
</section>

</div>
</body>
</html>
```